Church needs a street sign design

We're a small church located in Silicon Valley, California. Our website is https://www.vgtmarlowfield.org/ and our address is 4817 Ferrow Ave, San Jose, California, 95873. You can look up our location on Google Maps to see the sign from Street View. I have uploaded an image of the street sign as well. The marquee, the top section of the sign, and the separating line between them both will be removed. We're seeking a design for a new backlit acrylic insert that will go on the front of the light box and the back of the lightbox. The acrylic sign will fill the entire external frame. In the future, we may build a decorative wood frame around the structural legs, as visualized in one of the uploaded files. The church's brand colors are: #003366 (dark blue), #ff6600 (vibrant orange), #228b22 (forest green). I have also uploaded the church's logo assets. Our primary font is Montserrat and the secondary is Poppins. You can deviate from these colors/fonts if the sign is still coherent with the rest of our branding. Our branding values are mission, truth, passion, and community (please do not put those words on the sign! They are just intended to guide the look of the design). The sign dimensions are 96" by 47.5". Keep in mind that the sign will be backlit on a busy street side. It will also be positioned next to an old-looking church building. We do NOT want a sign that looks traditional, old, or antiquated. Instead, we want a modern-looking sign that pairs well with our old building while helping it look more modern too. We would also like the web address clearly visible on the sign: vgtmarlowfield.org. If you have any questions, just let me know!

```html
<!DOCTYPE html>
<html lang="en">
<head>
<meta charset="utf-8">
<title>Vine Grove Tabernacle – Street Sign</title>
<link href="https://fonts.googleapis.com/css2?family=Abril+Fatface&family=Montserrat:wght@300;400;600&family=Poppins:wght@700&display=swap" rel="stylesheet">
<style>
  :root {
    --brand-blue: #003366;
    --brand-orange: #ff6600;
    --sign-white: #ffffff;
    --script-tint: rgba(255, 255, 255, 0.22);
  }
  html, body {
    margin: 0;
    padding: 0;
    width: 1200px;
    height: 594px;
    overflow: hidden;
    background: var(--brand-blue);
  }
  .sign {
    position: relative;
    width: 1200px;
    height: 594px;
    background: var(--brand-blue);
    overflow: hidden;
  }

  /* Large decorative block on the left */
  .accent-square {
    position: absolute;
    left: 95px;
    top: 70px;
    width: 360px;
    height: 360px;
    border: 38px solid var(--brand-orange);
    border-radius: 10px;
    box-sizing: border-box;
    transform: rotate(-8deg);
  }

  /* Church name lockup */
  .name-square {
    position: absolute;
    left: 728px;
    top: 62px;
    width: 70px;
    height: 70px;
    border: 7px solid var(--sign-white);
    border-radius: 4px;
    box-sizing: border-box;
  }
  .church-name {
    position: absolute;
    right: 64px;
    top: 60px;
    margin: 0;
    text-align: right;
    font-family: "Montserrat", sans-serif;
    font-weight: 600;
    color: var(--sign-white);
    line-height: 1;
  }
  .church-name .name-main {
    display: block;
    font-size: 52px;
    letter-spacing: 1px;
  }
  .church-name .name-sub {
    display: block;
    margin-top: 10px;
    font-size: 22px;
    letter-spacing: 1px;
  }

  /* Headline */
  .script-word {
    position: absolute;
    left: 636px;
    top: 298px;
    width: 500px;
    height: 108px;
    border-radius: 10px;
    background: var(--script-tint);
  }
  .headline {
    position: absolute;
    left: 575px;
    top: 170px;
    width: 570px;
    height: 160px;
  }
  .headline svg { overflow: visible; display: block; }
  .headline-making {
    font-family: "Abril Fatface", serif;
    font-size: 168px;
    fill: var(--brand-orange);
  }

  .tagline {
    position: absolute;
    right: 72px;
    top: 405px;
    margin: 0;
    text-align: right;
    font-family: "Montserrat", sans-serif;
    font-weight: 400;
    font-size: 40px;
    line-height: 50px;
    color: var(--sign-white);
  }
  .web-address {
    position: absolute;
    right: 72px;
    top: 513px;
    margin: 0;
    font-family: "Montserrat", sans-serif;
    font-weight: 300;
    font-size: 31px;
    letter-spacing: 2px;
    color: var(--sign-white);
  }
  .web-address .domain {
    font-family: "Poppins", sans-serif;
    font-weight: 700;
    color: var(--brand-orange);
    letter-spacing: 2px;
  }
</style>
</head>
<body>
  <main class="sign">
    <div class="accent-square" aria-hidden="true"></div>

    <div class="name-square" aria-hidden="true"></div>
    <h1 class="church-name">
      <span class="name-main">VINE GROVE</span>
      <span class="name-sub">TABERNACLE</span>
    </h1>

    <div class="script-word" role="img" aria-label="Hand-lettered word 'disciples' in white brush script beneath the headline"></div>
    <div class="headline">
      <svg width="570" height="160" viewBox="0 0 570 160">
        <text class="headline-making" x="8" y="136" textLength="552" lengthAdjust="spacingAndGlyphs">Making</text>
      </svg>
    </div>

    <p class="tagline">&amp; Helping the Helpless<br>For the Glory of Christ</p>

    <p class="web-address">www.<span class="domain">vgtmarlowfield</span>.org</p>
  </main>
</body>
</html>
```